Develop website for Cloud Security Startup

Looking for a logo that conveys the outsourced security and management of clients data, systems and development in Tellix, Bri and Pindle with an emphasis on security and compliance

Target Market(s)

Companies looking for professional services IT firm

Coding

Coded - Design and coding required

Number of Pages Required

5+ page

Font styles to use
Sans Serif

Colors
0455a3
33a6d7

Requirements
Must have
• Landing Page
- Help me get started

Move to the cloud safely
- Benefits of Cloud

What we do
- Cloud Adoption
- Managed Services
- Optimise

Resources
- News
- Resources
- Events
- Webinars
- Not for profit
- Case Studies
- Support Button
- Incident Button

Company
- About Us
- Why Vorplexa?
- Acreditations
- Quorvane Tellix Partner
- Net Promoter Score
- Careers
- Contact Us

Contact Us

```html
<!DOCTYPE html>
<html lang="en">
<head>
<meta charset="utf-8">
<title>Vorplexa — Cloud Security</title>
<link href="https://fonts.googleapis.com/css2?family=Roboto:wght@400;500;700;900&display=swap" rel="stylesheet">
<style>
:root{
  --brand:#0455a3;
  --brand-light:#33a6d7;
  --navy:#061a3a;
  --ink:#1b1f2a;
  --muted:#6b7280;
  --line:#e3e8ef;
  --white:#ffffff;
  --sky:#2f8fd0;
}
*{margin:0;padding:0;box-sizing:border-box}
html,body{width:1200px;height:3948px;overflow:hidden}
body{font-family:"Roboto",Arial,sans-serif;color:var(--ink);background:var(--white);position:relative}
.abs{position:absolute}
.btn{display:inline-flex;align-items:center;gap:8px;background:var(--brand);color:var(--white);font-size:12px;font-weight:700;letter-spacing:.5px;padding:0 18px;height:38px;border-radius:3px;text-transform:uppercase}
.btn .dot{width:13px;height:13px;border-radius:50%;background:var(--white);display:inline-block;position:relative}
.btn .dot::after{content:"";position:absolute;left:4px;top:3.5px;border-left:5px solid var(--brand);border-top:3px solid transparent;border-bottom:3px solid transparent}

/* header */
.site-header{left:0;top:0;width:1200px;height:64px;background:var(--white);box-shadow:0 2px 6px rgba(0,0,0,.08);z-index:2}
.brand{display:flex;align-items:center;gap:8px;font-weight:900;color:var(--brand);font-size:20px;letter-spacing:.5px}
.brand .mark{width:22px;height:22px;border-radius:50%;background:var(--brand-light)}
.site-header .brand{position:absolute;left:40px;top:20px}
.main-nav{position:absolute;left:340px;top:0;height:64px;display:flex;gap:28px;align-items:center;font-size:12px;font-weight:700}
.site-header .btn{position:absolute;right:110px;top:13px;background:var(--brand-light)}

/* hero */
.hero{left:0;top:64px;width:1200px;height:568px;background:linear-gradient(100deg,#030d22 0%,#0a2654 45%,#1b5aa0 70%,#0b1e40 100%)}
.hero h1{position:absolute;left:110px;top:180px;color:var(--white);font-size:58px;font-weight:900;letter-spacing:1px}
.hero p{position:absolute;left:110px;top:258px;width:460px;color:#dce7f7;font-size:14px;line-height:1.5}
.hero .btn{position:absolute;left:110px;top:332px;background:var(--brand-light)}

/* about */
.about-art{left:120px;top:690px;width:320px;height:320px;border-radius:24px;background:linear-gradient(135deg,var(--brand-light),var(--brand))}
.about h2,.section-title{font-size:30px;font-weight:900;letter-spacing:.5px}
.about{left:620px;top:720px;width:470px}
.about p{margin-top:18px;font-size:13px;line-height:1.75;color:var(--muted)}
.about .btn{margin-top:22px}
.section-title{width:1200px;left:0;text-align:center}

/* services */
.service{background:var(--white);border:1px solid var(--line);box-shadow:0 4px 14px rgba(0,0,0,.06);text-align:center;padding:40px 30px}
.service.active{background:var(--brand-light);color:var(--white);border:none}
.service .icon{width:64px;height:64px;margin:0 auto}
.service h3{font-size:14px;font-weight:700;margin-top:24px}
.service p{font-size:12px;line-height:1.6;color:var(--muted);margin-top:12px}
.service.active p{color:#eaf6fc}

/* benefits */
.benefits-band{left:0;top:1728px;width:700px;height:464px}
.benefits{left:100px;top:1790px;width:460px;color:var(--white)}
.benefits h2{font-size:30px;font-weight:900}
.benefits p{font-size:12px;line-height:1.6;margin-top:16px;color:#e6f2fb}
.benefits ul{list-style:none;margin-top:24px}
.benefits li{display:flex;align-items:center;gap:14px;font-size:12px;font-weight:700;margin-bottom:22px}
.benefits .btn{margin-top:8px;background:var(--brand)}
.benefits-art{left:690px;top:1740px;width:420px;height:440px;border-radius:30px;background:radial-gradient(circle at 50% 45%,#bfe6f7 0%,#6fbfe6 45%,#e8f5fc 80%)}

/* blog */
.post-main{left:110px;top:2392px;width:470px;height:628px;border:1px solid var(--line);box-shadow:0 4px 14px rgba(0,0,0,.08);background:var(--white)}
.post-main .thumb{height:248px;background:linear-gradient(135deg,#e9edf2,#9aa8b8 60%,#c9d2dc)}
.post-main .body{padding:26px 30px}
.post-main h3{font-size:15px;font-weight:700;line-height:1.5}
.meta{display:flex;gap:24px;font-size:11px;color:var(--muted);margin-top:16px}
.meta span::before{content:"";display:inline-block;width:9px;height:9px;background:var(--brand-light);margin-right:6px;border-radius:2px}
.post-main p{font-size:12px;line-height:1.7;color:var(--muted);margin-top:16px}
.post-main .btn{margin-top:22px}
.post-side{left:596px;width:494px;height:196px;display:flex;border:1px solid var(--line);box-shadow:0 4px 14px rgba(0,0,0,.08);background:var(--white)}
.post-side .thumb{width:184px;height:100%}
.post-side .body{padding:22px 20px}
.post-side h4{font-size:13px;font-weight:700;line-height:1.5}
.post-side p{font-size:12px;line-height:1.6;color:var(--muted);margin-top:10px}

/* contact */
.contact{left:0;top:3028px;width:1200px;height:732px;background:linear-gradient(180deg,#3aa3d9 0%,#2a8fcf 55%,#1f7ec4 100%)}
.contact .section-title{top:62px;color:var(--white)}
.field{position:absolute;background:var(--white);font-size:12px;color:#555;padding:12px 14px;height:42px}
.contact .btn{position:absolute;left:525px;top:420px;background:var(--brand)}
.info{position:absolute;top:508px;display:flex;align-items:center;gap:14px;color:var(--white);font-size:13px;font-weight:700;line-height:1.4}
.info .ring{width:50px;height:50px;border-radius:50%;border:2px solid var(--white);display:flex;align-items:center;justify-content:center}

/* footer */
.site-footer{left:0;top:3760px;width:1200px;height:188px;background:var(--brand);color:var(--white);text-align:center}
.site-footer .brand{color:var(--white);justify-content:center;margin-top:26px}
.site-footer .brand .mark{background:var(--white)}
.foot-nav{display:flex;justify-content:center;gap:30px;font-size:12px;font-weight:700;margin-top:30px}
.copy{font-size:11px;margin-top:20px;color:#d5e6f7}
</style>
</head>
<body>

<header class="site-header abs">
  <div class="brand"><span class="mark"></span>VORPLEXA</div>
  <nav class="main-nav"><span>HOME</span><span>WHAT WE DO</span><span>RESOURCES</span><span>COMPANY</span><span>CONTACT US</span></nav>
  <span class="btn">Help me get started</span>
</header>

<section class="hero abs" role="img" aria-label="Photo of a hand holding a phone beneath a glowing cloud with a security lock">
  <h1>VORPLEXA</h1>
  <p>Lorem ipsum dolor sit amet, consectetur adipiscing elit, sed do eiusmod tempor incididunt ut labore et dolore magna aliqua.</p>
  <span class="btn">Get started <span class="dot"></span></span>
</section>

<div class="about-art abs" role="img" aria-label="Brand illustration in blue tones"></div>
<section class="about abs">
  <h2>ABOUT US</h2>
  <p>Sed ut perspiciatis unde omnis iste natus error sit voluptatem accusantium doloremque laudantium, totam rem aperiam, eaque ipsa quae ab illo inventore veritatis et quasi architecto beatae vitae dicta sunt explicabo. Nemo enim ipsam voluptatem quia voluptas sit aspernatur aut odit aut fugit, sed quia consequuntur magni dolores eos qui ratione voluptatem sequi nesciunt. Neque porro quisquam est, qui dolorem ipsum quia dolor sit amet. Ut enim ad minima veniam, quis nostrum exercitationem ullam corporis suscipit laboriosam, nisi ut aliquid ex ea commodi consequatur.</p>
  <span class="btn">Get started <span class="dot"></span></span>
</section>

<h2 class="section-title abs" style="top:1186px">WHAT WE DO</h2>

<article class="service abs" style="left:110px;top:1290px;width:320px;height:290px">
  <svg class="icon" viewBox="0 0 64 64"><circle cx="32" cy="32" r="30" fill="none" stroke="#0455a3" stroke-width="1.5"/><path d="M32 16l12 5v10c0 8-5 14-12 17-7-3-12-9-12-17V21z" fill="#0455a3"/></svg>
  <h3>CLOUD ADOPTION</h3>
  <p>Sed ut perspiciatis unde omnis iste natus error sit voluptatem accusantium doloremque laudantium, totam rem.</p>
</article>
<article class="service active abs" style="left:440px;top:1280px;width:320px;height:312px">
  <svg class="icon" viewBox="0 0 64 64"><circle cx="32" cy="32" r="30" fill="none" stroke="#fff" stroke-width="1.5"/><rect x="21" y="29" width="22" height="17" rx="2" fill="#fff"/><path d="M25 29v-5a7 7 0 0 1 14 0v5" fill="none" stroke="#fff" stroke-width="3"/></svg>
  <h3>MANAGED SERVICES</h3>
  <p>Sed ut perspiciatis unde omnis iste natus error sit voluptatem accusantium doloremque laudantium, totam rem.</p>
</article>
<article class="service abs" style="left:770px;top:1290px;width:320px;height:290px">
  <svg class="icon" viewBox="0 0 64 64"><circle cx="32" cy="32" r="30" fill="none" stroke="#0455a3" stroke-width="1.5"/><rect x="18" y="20" width="28" height="20" rx="2" fill="none" stroke="#0455a3" stroke-width="3"/><path d="M26 46h12M32 40v6" stroke="#0455a3" stroke-width="3"/></svg>
  <h3>OPTIMISE</h3>
  <p>Sed ut perspiciatis unde omnis iste natus error sit voluptatem accusantium doloremque laudantium, totam rem.</p>
</article>

<svg class="benefits-band abs" viewBox="0 0 700 464" preserveAspectRatio="none" aria-hidden="true">
  <defs><linearGradient id="band" x1="0" x2="1"><stop offset="0" stop-color="#33a6d7"/><stop offset="1" stop-color="#0f7cc4"/></linearGradient></defs>
  <path d="M0 0H520C700 80 700 380 520 464H0Z" fill="url(#band)"/>
</svg>
<section class="benefits abs">
  <h2>BENEFITS</h2>
  <p>Sed ut perspiciatis unde omnis iste natus error sit voluptatem accusantium doloremque.</p>
  <ul>
    <li><svg width="26" height="18" viewBox="0 0 26 18"><path d="M7 17a6 6 0 0 1 0-12 7 7 0 0 1 13 2 5 5 0 0 1 0 10z" fill="#fff"/></svg>LOREM IPSUM DOLOR SIT</li>
    <li><svg width="26" height="18" viewBox="0 0 26 18"><path d="M7 17a6 6 0 0 1 0-12 7 7 0 0 1 13 2 5 5 0 0 1 0 10z" fill="#fff"/></svg>LOREM IPSUM DOLOR SIT</li>
    <li><svg width="26" height="18" viewBox="0 0 26 18"><path d="M7 17a6 6 0 0 1 0-12 7 7 0 0 1 13 2 5 5 0 0 1 0 10z" fill="#fff"/></svg>LOREM IPSUM DOLOR SIT</li>
  </ul>
  <span class="btn">Get started <span class="dot"></span></span>
</section>
<div class="benefits-art abs" role="img" aria-label="Illustration of a cloud with padlocks connected to servers"></div>

<h2 class="section-title abs" style="top:2290px">LATEST BLOG</h2>

<article class="post-main abs">
  <div class="thumb" role="img" aria-label="Photo of a hand touching a digital security padlock"></div>
  <div class="body">
    <h3>SED UT PERSPICIATIS UNDE OMNIS ISTE NATUS ERROR SIT VOLUPTATEM ACCUSANTIUM</h3>
    <div class="meta"><span>05/06/2021</span><span>WP Room Update</span><span>1,368</span></div>
    <p>Nemo enim ipsam voluptatem quia voluptas sit aspernatur aut odit aut fugit, sed quia consequuntur magni dolores.</p>
    <span class="btn">Read more <span class="dot"></span></span>
  </div>
</article>
<article class="post-side abs" style="top:2392px">
  <div class="thumb" role="img" aria-label="Photo of a server room" style="background:linear-gradient(135deg,#0d2b4f,#2f6fa8)"></div>
  <div class="body"><h4>ET HARUM QUIDEM RERUM FACILIS EST ET</h4><p>Ut enim ad minima veniam, quis nostrum sed quia consequuntur.</p></div>
</article>
<article class="post-side abs" style="top:2608px">
  <div class="thumb" role="img" aria-label="Photo of a person working in a data centre" style="background:linear-gradient(135deg,#1c3550,#5a7d9e)"></div>
  <div class="body"><h4>ET HARUM QUIDEM RERUM FACILIS EST ET</h4><p>Ut enim ad minima veniam, quis nostrum sed quia consequuntur.</p></div>
</article>
<article class="post-side abs" style="top:2824px">
  <div class="thumb" role="img" aria-label="Photo of a digital cloud above a laptop" style="background:linear-gradient(135deg,#0a2a55,#3aa0d8)"></div>
  <div class="body"><h4>ET HARUM QUIDEM RERUM FACILIS EST ET</h4><p>Ut enim ad minima veniam, quis nostrum sed quia consequuntur.</p></div>
</article>

<section class="contact abs">
  <h2 class="section-title abs">CONTACT US</h2>
  <div class="field" style="left:225px;top:162px;width:368px">Name</div>
  <div class="field" style="left:607px;top:162px;width:368px">Company</div>
  <div class="field" style="left:225px;top:216px;width:368px">Email</div>
  <div class="field" style="left:607px;top:216px;width:368px">Telephone</div>
  <div class="field" style="left:225px;top:270px;width:750px;height:104px">Message</div>
  <span class="btn">View more <span class="dot"></span></span>

  <div class="info" style="left:90px">
    <span class="ring"><svg width="20" height="24" viewBox="0 0 20 24"><path d="M10 23S2 14 2 9a8 8 0 0 1 16 0c0 5-8 14-8 14z" fill="#fff"/><circle cx="10" cy="9" r="3" fill="#2a8fcf"/></svg></span>
    <span>Lorem Ipsum Dolor<br>United States</span>
  </div>
  <div class="info" style="left:360px">
    <span class="ring"><svg width="24" height="24" viewBox="0 0 24 24" fill="none" stroke="#fff" stroke-width="2"><circle cx="12" cy="12" r="10"/><path d="M2 12h20M12 2c3 3 3 17 0 20M12 2c-3 3-3 17 0 20"/></svg></span>
    <span>www.vorplexa.com</span>
  </div>
  <div class="info" style="left:640px">
    <span class="ring"><svg width="22" height="22" viewBox="0 0 24 24"><path d="M6 2l4 4-2 3c1 3 4 6 7 7l3-2 4 4-3 4C10 22 2 14 2 5z" fill="#fff"/></svg></span>
    <span>1 800 555 010</span>
  </div>
  <div class="info" style="left:900px">
    <span class="ring"><svg width="22" height="22" viewBox="0 0 24 24"><path d="M6 2l4 4-2 3c1 3 4 6 7 7l3-2 4 4-3 4C10 22 2 14 2 5z" fill="#fff"/></svg></span>
    <span>1 800 555 020</span>
  </div>
</section>

<footer class="site-footer abs">
  <div class="brand"><span class="mark"></span>VORPLEXA</div>
  <nav class="foot-nav"><span>HOME</span><span>WHAT WE DO</span><span>RESOURCES</span><span>COMPANY</span><span>CONTACT US</span></nav>
  <p class="copy">© 2021 Vorplexa. All Rights Reserved</p>
</footer>

</body>
</html>
```